Bright Pelvicare Business Card

Need a business card for a surgical practice called Bright Pelvicare. We have recently selected a logo (attached). The business card will need to have two formats:
1) One with the logo/physician name/ contact info on the front and location information on the back.
2) One in "appointment reminder card" style with the logo/ contact info/ date/ time on the front and the location information on the back.

The front side should include the following information:
- Logo
- Rohan K. Desai, MD FACOG
- phone: 469-555-0182
- fax: 1-469-555-0317
- email: admin@brightpelvi.com
- website: www.brightpelvicare.com

The back side should have the office locations listed:
4518 Kestrel Ave, Plano, TX 75198
3920 Bramwell Rd, Plano, TX 75147
2245 Silverpine Ln, Irving, TX 75163
815 W Garnet Ave S310, Dallas, TX 75284
3614 Lantern Blvd, Grand Prairie, TX 75179
7405 Amberly Crest Dr, San Antonio, TX 78391
5812 Tolliver Rd, Pasadena, TX 77639

Target Market(s)

1. Other physicians who might refer patients
2. Female patients

Industry/Entity Type

Business

Font styles to use
Other font styles liked:
• Tahoma for lettering

Requirements
Must have
• As per the instructions
Should not have
• No other images needed -- please try to keep font consistent with logo design. Can use Tahoma as the font for lettering.

```html
<!DOCTYPE html>
<html lang="en">
<head>
<meta charset="utf-8">
<title>Bright Pelvicare Business Card</title>
<link href="https://fonts.googleapis.com/css2?family=Lato:wght@400;700&display=swap" rel="stylesheet">
<style>
  :root {
    --page-bg: #ececec;
    --card-white: #fbfbfa;
    --ink-blue: #2c67a8;
    --ink-dark: #1c1f24;
    --brand-blue: #3a78b8;
    --art-red: #e8574d;
    --art-salmon: #f29a86;
    --art-blue-dark: #1f569b;
    --art-blue-light: #3b80bd;
    --back-blue-a: #4a80c2;
    --back-blue-b: #5c93e2;
    --back-ink: #16263a;
  }
  * { margin: 0; padding: 0; box-sizing: border-box; }
  html, body { width: 1200px; height: 720px; overflow: hidden; }
  body {
    background: var(--page-bg);
    font-family: "Lato", Tahoma, sans-serif;
    position: relative;
  }
  .card {
    position: absolute;
    top: 242px;
    width: 420px;
    height: 239px;
    overflow: hidden;
  }
  .card-front { left: 147px; background: var(--card-white); }
  .card-back {
    left: 633px;
    background: linear-gradient(120deg, var(--back-blue-a), var(--back-blue-b));
    text-align: center;
  }

  .wave-area {
    position: absolute;
    left: 0; right: 0; bottom: 0;
    height: 96px;
    background:
      linear-gradient(180deg, rgba(242,154,134,0.95) 0%, rgba(232,87,77,0.85) 30%, rgba(31,86,155,0) 62%),
      linear-gradient(90deg, var(--art-blue-dark), var(--art-blue-light));
  }

  .physician { position: absolute; left: 18px; top: 29px; }
  .physician-name { color: var(--ink-blue); font-weight: 700; font-size: 14px; line-height: 16px; }
  .physician-title { color: var(--ink-dark); font-size: 10px; line-height: 12px; }

  .contact-list { position: absolute; left: 18px; top: 78px; list-style: none; }
  .contact-item {
    display: flex; align-items: center; gap: 7px;
    font-size: 10px; line-height: 12.8px; color: var(--ink-dark);
  }
  .contact-icon { width: 11px; height: 9px; flex: none; }

  .brand { position: absolute; left: 210px; top: 22px; width: 200px; text-align: center; }
  .brand-dot { display: block; margin: 0 auto 4px; width: 22px; height: 22px; border-radius: 50%; background: var(--brand-blue); }
  .brand-name { color: var(--brand-blue); font-weight: 700; font-size: 18px; line-height: 20px; }

  .locations-title { color: #fff; font-weight: 700; font-size: 17px; margin-top: 38px; line-height: 22px; }
  .location-list { list-style: none; margin-top: 2px; }
  .location-list li { color: var(--back-ink); font-size: 13.5px; line-height: 20px; }
</style>
</head>
<body>
  <section class="card card-front">
    <div class="wave-area" role="img" aria-label="Flowing red and blue wave decoration across the lower card"></div>

    <div class="physician">
      <p class="physician-name">Rohan K. Desai</p>
      <p class="physician-title">MD FACOG</p>
    </div>

    <ul class="contact-list">
      <li class="contact-item">
        <svg class="contact-icon" viewBox="0 0 11 9"><path fill="var(--ink-blue)" d="M0,3 C1,0 10,0 11,3 L8,3.5 L7.5,2 L3.5,2 L3,3.5Z M2.5,4 L8.5,4 L10,9 L1,9Z"/></svg>
        469-555-0182
      </li>
      <li class="contact-item">
        <svg class="contact-icon" viewBox="0 0 11 9"><path fill="var(--ink-blue)" d="M3,0 H8 V2.5 H3Z M0,3 H11 V7 H9 V9 H2 V7 H0Z"/></svg>
        1-469-555-0317
      </li>
      <li class="contact-item">
        <svg class="contact-icon" viewBox="0 0 11 9"><rect width="11" height="9" fill="var(--ink-blue)"/><path d="M0.5,0.8 L5.5,5 L10.5,0.8" fill="none" stroke="#fff" stroke-width="1"/></svg>
        admin@brightpelvi.com
      </li>
      <li class="contact-item">
        <svg class="contact-icon" viewBox="0 0 11 9"><rect x="0.6" y="0.6" width="9.8" height="6" fill="none" stroke="var(--ink-blue)" stroke-width="1.2"/><rect x="3.5" y="7.5" width="4" height="1.5" fill="var(--ink-blue)"/></svg>
        www.brightpelvicare.com
      </li>
    </ul>

    <div class="brand">
      <span class="brand-dot"></span>
      <p class="brand-name">Bright Pelvicare</p>
    </div>
  </section>

  <section class="card card-back">
    <h2 class="locations-title">Office locations :</h2>
    <ul class="location-list">
      <li>4518 Kestrel Ave, Plano, TX 75198</li>
      <li>3920 Bramwell Rd, Plano, TX 75147</li>
      <li>2245 Silverpine Ln, Irving, TX 75163</li>
      <li>815 W Garnet Ave S310, Dallas, TX 75284</li>
      <li>3614 Lantern Blvd, Grand Prairie, TX 75179</li>
      <li>7405 Amberly Crest Dr, San Antonio, TX 78391</li>
      <li>5812 Tolliver Rd, Pasadena, TX 77639</li>
    </ul>
  </section>
</body>
</html>
```